Business card design

I am open to ideas. I was thinking of a vertical design, turning the name 90 degrees and placing it on the left edge, then some clipped portion of the fabulous tree with contact info on the bottom -- special emphasis on Web address:WhimBeads.comFor All Your Beading Needs121 E. Cotati AveCotati, CA 94931(707) 664-8343

```html
<!DOCTYPE html>
<html lang="en">
<head>
<meta charset="utf-8">
<title>Fern Glass Co. — Business Card</title>
<link href="https://fonts.googleapis.com/css2?family=Roboto:wght@300;400;500&display=swap" rel="stylesheet">
<style>
  :root {
    --backdrop: #4b433e;
    --card: #121212;
    --card-edge: #1c1c1c;
    --ink-bright: #f2f2f2;
    --ink-soft: #b9b9b9;
    --ink-silver: #dcdcdc;
    --mark-front: #e8e8e8;
    --mark-back: #cfcfcf;
  }
  * { box-sizing: border-box; margin: 0; padding: 0; }
  html, body {
    width: 1200px;
    height: 844px;
    overflow: hidden;
    background: var(--backdrop);
    font-family: "Roboto", Arial, sans-serif;
  }
  .canvas {
    position: relative;
    width: 1200px;
    height: 844px;
    display: flex;
    align-items: center;
    justify-content: center;
    gap: 48px;
  }
  .card {
    position: relative;
    width: 525px;
    height: 300px;
    background: var(--card);
    border: 1px solid var(--card-edge);
    box-shadow: 0 10px 30px rgba(0,0,0,0.45);
    overflow: hidden;
  }

  /* Shared brand lockup: plain circle above the name */
  .brand {
    display: flex;
    flex-direction: column;
    align-items: center;
    gap: 10px;
  }
  .brand-mark {
    border-radius: 50%;
  }
  .brand-name {
    font-weight: 400;
    letter-spacing: 0.5px;
    white-space: nowrap;
  }

  /* Front side */
  .front .brand {
    position: absolute;
    top: 30px;
    right: 40px;
    width: 250px;
  }
  .front .brand-mark {
    width: 118px;
    height: 118px;
    background: var(--mark-front);
  }
  .front .brand-name {
    font-size: 30px;
    color: var(--ink-bright);
  }
  .contact {
    position: absolute;
    left: 34px;
    bottom: 30px;
    color: var(--ink-soft);
  }
  .contact .phone {
    font-weight: 500;
    font-size: 21px;
    color: var(--ink-bright);
    margin-bottom: 14px;
  }
  .contact .address {
    font-weight: 300;
    font-size: 16px;
    line-height: 1.35;
    margin-bottom: 12px;
  }
  .contact .website {
    font-weight: 400;
    font-size: 24px;
    color: var(--ink-bright);
  }

  /* Back side */
  .back {
    display: flex;
    flex-direction: column;
    align-items: center;
    justify-content: center;
  }
  .back .brand {
    gap: 12px;
    margin-bottom: 16px;
  }
  .back .brand-mark {
    width: 128px;
    height: 128px;
    background: var(--mark-back);
  }
  .back .brand-name {
    font-size: 32px;
    color: var(--ink-silver);
  }
  .tagline {
    font-weight: 400;
    font-size: 12px;
    letter-spacing: 1px;
    text-transform: uppercase;
    color: var(--ink-bright);
  }
</style>
</head>
<body>
  <main class="canvas">
    <section class="card front" aria-label="Card front">
      <div class="brand">
        <span class="brand-mark"></span>
        <span class="brand-name">Fern Glass Co.</span>
      </div>
      <div class="contact">
        <p class="phone">(707) 555-0192</p>
        <p class="address">348 W. Brindle Ave<br>Alder Creek, CA 94920</p>
        <p class="website">www.FernGlassco.com</p>
      </div>
    </section>

    <section class="card back" aria-label="Card back">
      <div class="brand">
        <span class="brand-mark"></span>
        <span class="brand-name">Fern Glass Co.</span>
      </div>
      <p class="tagline">For all your beading needs</p>
    </section>
  </main>
</body>
</html>
```